Website for Torvel Capital - investment banking firm

We have a corporate identity (thanks to Ravinka/31842) and want to extend that into a website design.  See the attached zipped files.
We have software folks in-house to do the coding.
See the attached Project Brief & Notes for more details.  Don't worry about the actual text - lorem ipsum will be fine.
The server will be Apache.
Thank you!
Desmond

Industry/Entity Type
Investment

```html
<!DOCTYPE html>
<html lang="en">
<head>
<meta charset="utf-8">
<title>Torvel Capital</title>
<link href="https://fonts.googleapis.com/css2?family=Cinzel:wght@400;700&family=Lato:ital,wght@0,400;0,700;1,400&family=Ubuntu:wght@400&display=swap" rel="stylesheet">
<style>
:root{
  --navy:#0b3a78;
  --blue:#1f4f9c;
  --nav-top:#2456a3;
  --nav-bot:#163d80;
  --nav-active:#4d88c9;
  --ink:#2b2b2b;
  --grey:#666;
  --rule:#c9ced6;
  --footer:#0b3a78;
  --btn:#4d9ad9;
}
*{margin:0;padding:0;box-sizing:border-box}
html,body{width:1200px;height:1148px;overflow:hidden}
body{position:relative;background:#fff;font-family:"Lato",sans-serif;color:var(--ink)}
.abs{position:absolute}

/* header */
.site-header{position:absolute;left:0;top:0;width:1200px;height:95px;background:#fff}
.follow{left:131px;top:39px;font-family:"Cinzel",serif;font-weight:700;font-size:19px;color:var(--blue);letter-spacing:.3px;white-space:nowrap}
.social{top:39px;width:25px;height:25px;border-radius:50%;background:#6f6f6f}
.brand{left:431px;top:16px;height:66px;display:flex;align-items:center}
.brand-mark{width:52px;height:52px;background:var(--blue)}
.brand-rule{width:2px;height:64px;background:#777;margin:0 14px 0 16px}
.brand-name{font-family:"Cinzel",serif;font-weight:700;font-size:34px;color:var(--blue);letter-spacing:.3px;white-space:nowrap}
.question{left:848px;top:29px}
.question-text{position:absolute;left:51px;top:0;white-space:nowrap;font-family:"Cinzel",serif;font-weight:700;font-size:16px;color:var(--blue)}
.question-number{position:absolute;left:51px;top:17px;white-space:nowrap;font-family:"Cinzel",serif;font-size:25px;line-height:28px;color:#333}

/* nav */
.main-nav{position:absolute;left:0;top:95px;width:1200px;height:41px;background:linear-gradient(var(--nav-top),var(--nav-bot))}
.main-nav ul{list-style:none;position:absolute;left:131px;top:0;display:flex;height:41px}
.main-nav li{height:41px;display:flex;align-items:center;justify-content:center;font-family:"Cinzel",serif;font-size:16px;color:#fff;letter-spacing:.6px;border-right:1px solid #0e2f68;box-shadow:inset -1px 0 0 #3767b0;white-space:nowrap}
.main-nav li.active{background:linear-gradient(#5e9bd6,#3a73b8)}

/* hero */
.hero-backdrop{position:absolute;left:0;top:136px;width:1200px;height:792px;background:linear-gradient(90deg,#e4e7ea,#f4f6f8 10%,#f4f6f8 90%,#e2e5e8)}
.hero-photo{position:absolute;left:131px;top:136px;width:938px;height:516px;background:linear-gradient(160deg,#b8c9dc 0%,#8ea7c2 35%,#5d6f82 60%,#2b3550 85%,#1d2540 100%)}
.hero-caption{position:absolute;left:131px;top:464px;width:500px;height:149px;background:rgba(240,240,240,.85);padding:12px 0 0 17px}
.hero-caption h1{font-family:"Cinzel",serif;font-weight:700;font-size:36px;text-transform:uppercase;color:var(--blue);line-height:1.1;letter-spacing:.3px;white-space:nowrap}
.hero-caption p{font-family:"Ubuntu",sans-serif;font-size:20px;line-height:27px;color:#333;margin-top:6px;width:460px}

/* footer */
.site-footer{position:absolute;left:0;top:928px;width:1200px;height:220px;background:var(--footer)}
.footer-links{position:absolute;left:137px;top:1016px;font-size:13.5px;color:#fff;white-space:nowrap}
.footer-links span{margin:0 8px;color:#c9d5e6}
.newsletter{position:absolute;left:134px;top:1054px;height:34px}
.nl-icon{position:absolute;left:0;top:0;width:34px;height:34px;border-radius:50%;background:var(--navy);border:2px solid #fff;display:flex;align-items:center;justify-content:center;z-index:1}
.nl-input{position:absolute;left:30px;top:0;width:148px;height:34px;background:#fff;border-radius:3px;font-size:11px;color:#999;padding:10px 0 0 14px;white-space:nowrap}
.nl-button{position:absolute;left:183px;top:0;width:84px;height:34px;background:var(--btn);border-radius:3px;border:1px solid #79b6e6;color:#fff;font-size:14px;display:flex;align-items:center;justify-content:center}
.copyright{position:absolute;left:134px;top:1106px;font-size:12.5px;color:#fff;white-space:nowrap}
.contact{position:absolute;left:795px;color:#fff;font-size:13.5px;line-height:16px}
.contact svg{position:absolute;left:0}
.contact div{position:absolute;left:26px;white-space:nowrap}

/* content */
.content-panel{position:absolute;z-index:2;left:131px;top:652px;width:938px;height:337px;background:#fff;box-shadow:0 2px 6px rgba(0,0,0,.15)}
.col-title{position:absolute;top:32px;white-space:nowrap;font-family:"Cinzel",serif;font-weight:700;font-size:23px;color:#333}
.col-title span{color:var(--blue)}
.col-rule{position:absolute;top:66px;height:1px;background:var(--rule)}
.col-rule::after{content:"";position:absolute;left:8px;top:0;width:10px;height:10px;border-right:1px solid var(--rule);border-bottom:1px solid var(--rule);background:#fff;transform:rotate(45deg) translate(-2px,-6px)}
.divider{position:absolute;top:60px;width:1px;height:230px;background:linear-gradient(#fff,#dcdfe4 40%,#fff)}
.read-more{position:absolute;top:290px;font-size:13.5px;font-weight:700;color:#333;white-space:nowrap}

.about-photo{position:absolute;left:16px;top:81px;width:268px;height:103px;background:linear-gradient(90deg,#c7ccd2,#e8e1da 40%,#3b4658 70%,#c9b8a8)}
.about-text{position:absolute;left:16px;top:199px;width:272px;font-size:12.8px;line-height:19.5px;letter-spacing:.3px;color:#333}

.service{position:absolute;left:342px;width:264px;display:flex;align-items:center}
.service-icon{width:44px;height:40px;display:flex;align-items:center;justify-content:flex-start}
.service-sep{width:1px;height:22px;background:#ccc;margin-right:10px}
.service-name{font-size:15px;font-weight:700;color:#333;line-height:18px;white-space:nowrap}
.service-rule{position:absolute;left:342px;width:264px;height:2px;background:linear-gradient(#e5e7ea,#fff)}

.quote{position:absolute;left:659px;top:80px;width:263px;height:130px;background:#e3e5e8;border-radius:6px;padding:12px 6px 0 12px;font-style:italic;font-size:12.5px;line-height:22.5px;color:#333}
.quote::after{content:"";position:absolute;right:36px;bottom:-22px;border-left:40px solid transparent;border-top:22px solid #e3e5e8}
.quote-mark{font-family:Georgia,serif;font-style:normal;font-size:34px;color:#b4b8be;line-height:16px;vertical-align:-10px;margin-right:6px}
.avatar{position:absolute;left:671px;top:197px;width:66px;height:67px;border:2px solid #fff;border-radius:4px;box-shadow:0 1px 3px rgba(0,0,0,.35);background:linear-gradient(#c9b39d,#2e3a52)}
.client-name{position:absolute;left:749px;top:241px;font-size:13px;color:#222;white-space:nowrap}
</style>
</head>
<body>

<header class="site-header">
  <div class="abs follow">Follow Us :</div>
  <div class="abs social" style="left:262px"></div>
  <div class="abs social" style="left:295px"></div>
  <div class="abs social" style="left:328px"></div>

  <div class="abs brand">
    <div class="brand-mark"></div>
    <div class="brand-rule"></div>
    <div class="brand-name">Torvel Capital</div>
  </div>

  <div class="abs question">
    <svg width="40" height="40" viewBox="0 0 40 40" class="abs" style="left:0;top:0">
      <circle cx="20" cy="20" r="18.5" fill="none" stroke="#444" stroke-width="2.5"/>
      <path d="M14 11c-2 1-3 3-2 6 2 6 6 10 12 12 3 1 5 0 6-2l-4-4-3 2c-3-1-5-4-6-6l2-3z" fill="#444"/>
    </svg>
    <div class="question-text">Have a Question ?</div>
    <div class="question-number">555-310-7482</div>
  </div>
</header>

<nav class="main-nav">
  <ul>
    <li class="active" style="width:99px">Home</li>
    <li style="width:92px">About</li>
    <li style="width:109px">Services</li>
    <li style="width:235px">Current Engagements</li>
    <li style="width:257px">Completed Transactions</li>
    <li style="width:146px;border-right:0;box-shadow:none">Contact Us</li>
  </ul>
</nav>

<div class="hero-backdrop" role="img" aria-label="Bright office interior with large windows"></div>
<div class="hero-photo" role="img" aria-label="Businessman in a suit leaning on a railing overlooking a harbour with cranes and city skyline"></div>
<div class="hero-caption">
  <h1>Torvel Capital LLC is</h1>
  <p>Dallas-based private investment banking advisory firm that acts as an intermediary on behalf of buyers &amp; sellers of private companies.</p>
</div>

<footer class="site-footer"></footer>

<section class="content-panel">
  <div class="col-title" style="left:22px">About <span>Torvel</span> Capital</div>
  <div class="col-rule" style="left:24px;width:282px"></div>
  <div class="about-photo" role="img" aria-label="Business team meeting around a table"></div>
  <p class="about-text">Torvel Capital's history in mergers and acquisitions traces back to 1998. We pride our selves in successfully matching buyers with sellers and enabling shareholders of all .</p>
  <div class="read-more" style="left:209px">Read More »</div>

  <div class="divider" style="left:322px"></div>

  <div class="col-title" style="left:342px">What <span>We Do</span></div>
  <div class="col-rule" style="left:342px;width:264px"></div>

  <div class="service" style="top:82px">
    <div class="service-icon">
      <svg width="40" height="30" viewBox="0 0 40 30"><path d="M2 10l8-6 8 3 6-3 8 2 6 6-8 9-4 4-4-1-3-3-4-1-8-5z" fill="none" stroke="#666" stroke-width="2.2" stroke-linejoin="round"/><path d="M16 10l6 4 6-2" fill="none" stroke="#666" stroke-width="2"/></svg>
    </div>
    <div class="service-sep"></div>
    <div class="service-name">Buy-Side Acquisitions</div>
  </div>
  <div class="service-rule" style="top:126px"></div>

  <div class="service" style="top:146px">
    <div class="service-icon">
      <svg width="36" height="36" viewBox="0 0 36 36"><text x="10" y="12" font-family="Lato" font-weight="700" font-size="13" fill="#666">$</text><rect x="3" y="24" width="5" height="10" fill="#666"/><rect x="10" y="20" width="5" height="14" fill="#666"/><rect x="17" y="16" width="5" height="18" fill="#666"/><rect x="24" y="12" width="5" height="22" fill="#666"/><path d="M3 20l12-8 6 3 10-8" fill="none" stroke="#666" stroke-width="2"/></svg>
    </div>
    <div class="service-sep"></div>
    <div class="service-name">Recapitalizations &amp;<br>Growth Capital Partnerships</div>
  </div>
  <div class="service-rule" style="top:196px"></div>

  <div class="service" style="top:216px">
    <div class="service-icon">
      <svg width="34" height="36" viewBox="0 0 34 36"><text x="11" y="14" font-family="Lato" font-weight="700" font-size="15" fill="#666">$</text><path d="M2 22h10l6 3h6l6-4 2 2-8 9H8l-6-3z" fill="#666"/></svg>
    </div>
    <div class="service-sep"></div>
    <div class="service-name">Sell-Side Transactions</div>
  </div>
  <div class="read-more" style="left:529px">Read More »</div>

  <div class="divider" style="left:622px"></div>

  <div class="col-title" style="left:658px">Client <span>Testimonials</span></div>
  <div class="col-rule" style="left:659px;width:264px"></div>
  <div class="quote"><span class="quote-mark">“</span>Duis autem vel eum iriureol hder in a vultat velit esse moles conqat vela ilu adipsin &nbsp;feugiat.Duis autem vel eum ure hendrern vultat velit esse autm vel eum iriure dol</div>
  <div class="avatar" role="img" aria-label="Client portrait"></div>
  <div class="client-name">Mr. Dolore Eu Feugiat</div>
  <div class="read-more" style="left:845px">Read More »</div>
</section>

<div class="footer-links">Home<span>|</span>About<span>|</span>Services<span>|</span>Current Engagements<span>|</span>Completed Transactions<span>|</span>Contact Us</div>

<div class="newsletter">
  <div class="nl-icon">
    <svg width="18" height="13" viewBox="0 0 18 13"><rect x="1" y="1" width="16" height="11" fill="none" stroke="#fff" stroke-width="1.6"/><path d="M1 1l8 6 8-6" fill="none" stroke="#fff" stroke-width="1.6"/></svg>
  </div>
  <div class="nl-input">Sign Up for Newsletter</div>
  <div class="nl-button">SUBSCRIBE</div>
</div>
<div class="copyright">© Copyright 2014 Torvel Capital. | All Rights Reserved</div>

<div class="contact" style="top:1012px">
  <svg width="14" height="20" viewBox="0 0 14 20" style="top:1px"><path d="M7 1a6 6 0 0 0-6 6c0 5 6 12 6 12s6-7 6-12a6 6 0 0 0-6-6z" fill="#fff"/><circle cx="7" cy="7" r="2.4" fill="#0b3a78"/></svg>
  <div>Hong Kong: Room 1408 Harbourline Centre<br>21 - 37 Kestrel Road East<br>Eastbay, Hong Kong</div>
</div>
<div class="contact" style="top:1071px">
  <svg width="18" height="16" viewBox="0 0 18 16" style="top:1px"><path d="M4 14c-1 0-2-1-1-3 3-5 7-8 11-10l2 2-3 3-2-1c-2 1-4 3-5 5l1 2-3 2z" fill="#fff"/></svg>
  <div style="font-weight:700;letter-spacing:.5px">555-310-7482</div>
</div>
<div class="contact" style="top:1099px">
  <svg width="16" height="12" viewBox="0 0 16 12" style="top:3px"><rect x="0.5" y="0.5" width="15" height="11" fill="#fff"/><path d="M0.5 0.5l7.5 6 7.5-6" fill="none" stroke="#0b3a78" stroke-width="1.2"/></svg>
  <div style="letter-spacing:.5px">info@torvelcapital.com</div>
</div>

</body>
</html>
```